Business card design

I need my logo on this card, things I need the card to have on it
licensed and insured.
owner operators Milo & Trent Halvorsen
my phone number 5083716254
Disaster Recovery, Storm Damage Restoration, Proactive Disaster Plan Management, Roof Repair/Restoration Structural Repair and Reconstruction, Emergency Boarding and Tarping Service, Perimeter Fencing, Emergency Tree Removal,

```html
<!DOCTYPE html>
<html lang="en">
<head>
<meta charset="UTF-8">
<title>Halvorsen's Construction – Business Card</title>
<link rel="stylesheet" href="https://fonts.googleapis.com/css2?family=Montserrat:wght@400;500&family=Nunito:wght@400&display=swap">
<style>
  :root {
    --backdrop: #9c9c9c;
    --brand-blue: #3d95d3;
    --brand-blue-deep: #2f7fc1;
    --brand-grey: #6e6f73;
    --card-white: #ffffff;
    --ink: #1d1d1f;
  }
  * { margin: 0; padding: 0; box-sizing: border-box; }
  html, body { width: 1093px; height: 1200px; overflow: hidden; }
  body {
    background: var(--backdrop);
    position: relative;
    font-family: "Montserrat", sans-serif;
  }
  .card {
    position: absolute;
    border-radius: 18px;
    overflow: hidden;
    box-shadow: 0 2px 6px rgba(0,0,0,0.25);
  }
  /* Front */
  .card-front {
    left: 265px; top: 224px; width: 580px; height: 362px;
    background: var(--brand-blue);
    color: var(--card-white);
    text-align: center;
  }
  .brand-name {
    font-family: "Montserrat", sans-serif;
    font-weight: 400;
    line-height: 1.15;
  }
  .card-front .brand-name {
    position: absolute; left: 0; right: 0; top: 96px;
    font-size: 30px;
    color: var(--card-white);
  }
  .services-title {
    position: absolute; left: 0; right: 0; top: 222px;
    font-size: 18px; font-weight: 400;
    letter-spacing: -0.3px;
  }
  .services-rule {
    position: absolute; left: 219px; width: 137px; top: 249px;
    height: 1px; background: rgba(255,255,255,0.8);
  }
  .services-list {
    position: absolute; left: 0; right: 0; top: 266px;
    list-style: none;
    font-family: "Nunito", sans-serif;
    font-size: 13.8px;
    line-height: 25px;
  }
  .services-list .dot { font-size: 10px; vertical-align: 2px; margin: 0 3px 0 5px; }
  /* Back */
  .card-back {
    left: 261px; top: 619px; width: 596px; height: 363px;
    background: var(--card-white);
    color: var(--ink);
  }
  .card-back .brand-name {
    position: absolute; left: 40px; width: 240px; top: 132px;
    text-align: center;
    font-size: 24px;
    color: var(--brand-blue);
  }
  .divider {
    position: absolute; left: 293px; top: 84px;
    width: 1px; height: 175px; background: var(--brand-grey);
  }
  .contact {
    position: absolute; left: 304px; top: 82px;
  }
  .owner-names {
    font-size: 23.5px; font-weight: 400;
    color: var(--brand-blue-deep);
    letter-spacing: -0.2px;
  }
  .owner-role { font-size: 13px; margin-top: 1px; }
  .address { font-family: "Nunito", sans-serif; font-size: 13.5px; line-height: 16.5px; margin-top: 17px; }
  .contact-lines { list-style: none; margin-top: 14px; font-size: 13px; }
  .contact-lines li { display: flex; align-items: center; height: 23.5px; }
  .contact-lines svg { width: 15px; height: 15px; margin-right: 9px; flex: none; }
  .footer-band {
    position: absolute; left: 0; bottom: 0; width: 596px; height: 78px;
    background: linear-gradient(90deg, var(--brand-grey) 0%, #4a8cc4 35%, #4392d0 100%);
  }
</style>
</head>
<body>

<section class="card card-front">
  <div class="brand-name">Halvorsen's<br>Construction L.L.C</div>
  <h2 class="services-title">OUR SERVICES</h2>
  <div class="services-rule"></div>
  <ul class="services-list">
    <li><span class="dot">●</span>Disaster Recovery <span class="dot">●</span>Storm Damage Restoration <span class="dot">●</span>Proactive Disaster Plan Management</li>
    <li><span class="dot">●</span>Roof Repair/Restoration Structural Repair and Reconstruction <span class="dot">●</span>Perimeter Fencing</li>
    <li><span class="dot">●</span>Emergency Boarding and Tarping Service <span class="dot">●</span>Emergency Tree Removal</li>
  </ul>
</section>

<section class="card card-back">
  <div class="brand-name">Halvorsen's<br>Construction L.L.C</div>
  <div class="divider"></div>
  <div class="contact">
    <h1 class="owner-names">Milo &amp; Trent Halvorsen</h1>
    <p class="owner-role">owner operators</p>
    <p class="address">742 Cedar Hollow Lane<br>Brandon, MS 39042</p>
    <ul class="contact-lines">
      <li>
        <svg viewBox="0 0 16 16" aria-hidden="true"><path fill="#3d95d3" d="M1 6c0-2 3-3 7-3s7 1 7 3v1h-3V5.5H4V7H1zM4 8h8l2 6H2z"/><circle cx="8" cy="11" r="1.6" fill="#fff"/></svg>
        &nbsp;5083716254
      </li>
      <li>
        <svg viewBox="0 0 16 16" aria-hidden="true"><rect x="1" y="3" width="14" height="10" rx="1" fill="#3d95d3"/><path d="M1.5 4l6.5 5 6.5-5" stroke="#fff" stroke-width="1.2" fill="none"/></svg>
        info@halvorsens.com
      </li>
      <li>
        <svg viewBox="0 0 16 16" aria-hidden="true"><circle cx="8" cy="8" r="7" fill="#3d95d3"/><path d="M4 4c2 1 1 3 3 3s1 3 0 4M10 3c-1 2 1 3 3 3M9 13c1-2 3-2 4-3" stroke="#fff" stroke-width="1.1" fill="none"/></svg>
        www.halvorsens.com
      </li>
    </ul>
  </div>
  <div class="footer-band" role="img" aria-label="Decorative grey and blue wave band along the bottom edge"></div>
</section>

</body>
</html>
```